Corvane Paintless Dent Removal

Our company works on vehicles removing dents using a highly skilled trade which the metal is massaged out with special tools without disturbing the original paint, hence paintless dent removal. Besides keeping the paint and metal original its also very environmentally friendly since no paint or toxic fillers are used. Also we we are one of the most experienced companies in the business with 25 years

Target Market(s)

Retail Automobile consumers, Auto Dealerships and Auto Body Shops

Industry/Entity Type

Auto Repair

Contact Information for Business Card

Dale Hollister
PO Box 518 Brookmere, NY 11962
631-555-0148
corvanepdr@mailbox-example.com
website corvanepdr.example
youtube corvane paintless dent removal
25 years of experience removing Dents, Dings and Hail Damage

Font styles to use
Serif
Sans Serif

Colors

Designer to choose colors to be used in the design.

Requirements
Must have
• I do like things that are simple but classy and somewhat bold, also I like my logo so that should be somewhat important

```html
<!DOCTYPE html>
<html lang="en">
<head>
<meta charset="utf-8">
<title>Corvane Paintless Dent Removal – Business Card</title>
<link rel="stylesheet" href="https://fonts.googleapis.com/css2?family=Roboto:wght@400;500;700&display=swap">
<style>
  :root {
    --navy: #10284a;
    --green: #7cc11f;
    --paper: #f4f4f4;
    --ink: #3a3f47;
    --gold: #d4a33a;
    --backdrop: #e6e3de;
  }
  * { margin: 0; padding: 0; box-sizing: border-box; }
  html, body { width: 1200px; height: 960px; overflow: hidden; }
  body {
    position: relative;
    background: var(--backdrop);
    font-family: "Roboto", Arial, sans-serif;
  }
  .card { position: absolute; width: 600px; height: 343px; box-shadow: 0 3px 8px rgba(0,0,0,.25); overflow: hidden; }
  .card--front { left: 314px; top: 113px; background: var(--paper); }
  .card--back { left: 311px; top: 472px; background: var(--navy); }

  .brand { position: absolute; display: flex; align-items: center; gap: 12px; font-weight: 700; line-height: 1; }
  .brand__dot { width: 18px; height: 18px; border-radius: 50%; background: var(--green); flex: none; }
  .brand__name { display: block; font-size: 36px; letter-spacing: .5px; }
  .brand__tag { display: block; font-size: 15px; margin-top: 5px; }
  .card--front .brand { left: 40px; top: 62px; color: var(--navy); }
  .card--back .brand { left: 0; right: 0; top: 136px; justify-content: center; color: #fff; }

  .holder { position: absolute; right: 46px; top: 80px; font-size: 21px; font-weight: 700; letter-spacing: .6px; color: var(--navy); }
  .accent-bar { position: absolute; right: 0; top: 75px; width: 16px; height: 32px; background: var(--green); }

  .contact { position: absolute; left: 56px; top: 199px; list-style: none; font-size: 14px; color: var(--ink); }
  .contact li { display: flex; align-items: center; height: 19.5px; }
  .contact svg { width: 12px; height: 12px; margin-right: 9px; fill: var(--navy); flex: none; }
  .contact .contact__plain { margin-left: 0; }

  .footer-band { position: absolute; left: 0; bottom: 0; width: 100%; height: 34px; background: var(--navy); }
  .footer-band__url { position: absolute; left: 55px; top: 9px; font-size: 14px; color: #fff; }

  .years-seal {
    position: absolute; left: 505px; top: 275px; width: 68px; height: 68px; border-radius: 50%;
    background: #151515; border: 4px solid var(--gold);
    display: flex; flex-direction: column; align-items: center; justify-content: center;
    color: var(--gold); font-weight: 700; line-height: 1;
  }
  .years-seal__num { font-size: 22px; }
  .years-seal__label { font-size: 8px; letter-spacing: .5px; margin-top: 1px; }

  .back-url { position: absolute; left: 0; right: 0; top: 280px; text-align: center; color: #fff; font-size: 14px; letter-spacing: 5.5px; }
</style>
</head>
<body>
  <section class="card card--front">
    <div class="brand">
      <span class="brand__dot"></span>
      <span><span class="brand__name">CORVANE</span><span class="brand__tag">Paintless Dent Removal</span></span>
    </div>
    <h1 class="holder">DALE HOLLISTER</h1>
    <span class="accent-bar"></span>

    <ul class="contact">
      <li><svg viewBox="0 0 24 24"><path d="M6.6 10.8a15.1 15.1 0 0 0 6.6 6.6l2.2-2.2c.3-.3.7-.4 1-.2 1.1.4 2.3.6 3.6.6.6 0 1 .4 1 1V20c0 .6-.4 1-1 1A17 17 0 0 1 3 4c0-.6.4-1 1-1h3.5c.6 0 1 .4 1 1 0 1.3.2 2.5.6 3.6.1.3 0 .7-.2 1z"/></svg>631-555-0148</li>
      <li><svg viewBox="0 0 24 24"><path d="M2 5h20v14H2z M4 7v.5l8 5 8-5V7l-8 5z" fill-rule="evenodd"/></svg>corvanepdr@mailbox-example.com</li>
      <li><svg viewBox="0 0 24 24"><rect x="3" y="5" width="18" height="14" rx="2"/></svg>corvane paintless dent removal</li>
      <li class="contact__plain">PO Box 518, Brookmere, NY 11962</li>
    </ul>

    <div class="footer-band"><span class="footer-band__url">www.corvanepdr.example</span></div>
    <div class="years-seal" aria-label="25 years of experience">
      <span class="years-seal__num">25</span>
      <span class="years-seal__label">YEARS</span>
    </div>
  </section>

  <section class="card card--back">
    <div class="brand">
      <span class="brand__dot"></span>
      <span><span class="brand__name">CORVANE</span><span class="brand__tag">Paintless Dent Removal</span></span>
    </div>
    <p class="back-url">www.corvanepdr.example</p>
  </section>
</body>
</html>
```